Need Business Card ASAP

We need a business card design for a meeting coming up in a few days. The company name is Harlow Ridge Building and Construction and the logo is attached. Something clean, cool, and contemporary that we can get to a printer right away. Attached is the business card for Volmar Energy, an affiliated company, which we like. Instead of the hawk on the back, you could use the attached "D". We'll also be needing matching letterhead in the near future, so ideas for that are welcome.

```html
<!DOCTYPE html>
<html lang="en">
<head>
<meta charset="utf-8">
<title>Harlow Ridge Building and Construction – Business Card</title>
<link rel="stylesheet" href="https://fonts.googleapis.com/css2?family=Source+Sans+3:wght@400;600;700&display=swap">
<style>
  :root {
    --backdrop: #8c6c4a;
    --card-white: #ffffff;
    --card-charcoal: #3c3c3c;
    --gold: #b7ac80;
    --gold-deep: #9f9468;
    --ink: #2a2a2a;
    --ink-soft: #3d3d3d;
    --divider: #c9c9c9;
  }
  * { box-sizing: border-box; margin: 0; padding: 0; }
  html, body {
    width: 1034px; height: 1200px; overflow: hidden;
    background: var(--backdrop);
    font-family: "Source Sans 3", Arial, sans-serif;
  }
  .canvas { position: relative; width: 1034px; height: 1200px; }

  .card { position: absolute; left: 68px; width: 889px; }
  .card--front { top: 59px; height: 507px; background: var(--card-white); }
  .card--back  { top: 586px; height: 521px; background: var(--card-charcoal); }

  /* Front */
  .brand-block {
    position: absolute; left: 181px; top: 105px; width: 170px; height: 218px;
    display: flex; flex-direction: column; justify-content: center; align-items: flex-start; gap: 16px;
  }
  .brand-square { width: 58px; height: 58px; background: var(--gold); }
  .brand-name {
    font-weight: 600; font-size: 25px; line-height: 1.15; color: var(--ink);
  }
  .divider {
    position: absolute; left: 380px; top: 103px; width: 2px; height: 222px;
    background: linear-gradient(to bottom, transparent, var(--divider) 15%, var(--divider) 85%, transparent);
  }
  .contact { position: absolute; left: 406px; top: 97px; }
  .contact__name { font-weight: 600; font-size: 31px; color: var(--gold); line-height: 1.1; }
  .contact__title { font-weight: 600; font-size: 21px; color: var(--ink-soft); margin-top: 4px; }
  .contact__list { list-style: none; margin-top: 18px; }
  .contact__item {
    display: flex; align-items: center; gap: 10px;
    font-size: 23px; color: var(--ink-soft); height: 39px;
  }
  .contact__item svg { width: 18px; height: 18px; flex: none; fill: var(--ink-soft); }

  .company { position: absolute; left: 0; right: 0; top: 372px; text-align: center; }
  .company__name { font-weight: 600; font-size: 30px; color: var(--gold); }
  .company__address { font-size: 21px; color: var(--ink); margin-top: 6px; }

  /* Back */
  .back-mark {
    position: absolute; left: 0; right: 0; top: 200px;
    text-align: center; font-weight: 600; font-size: 64px; color: var(--card-white);
    letter-spacing: 1px;
  }
  .back-url {
    position: absolute; left: 0; right: 0; top: 460px; text-align: center;
    font-weight: 700; font-size: 26px; color: var(--card-white); letter-spacing: 2.5px;
  }
</style>
</head>
<body>
<main class="canvas">
  <section class="card card--front">
    <div class="brand-block">
      <span class="brand-square"></span>
      <span class="brand-name">Harlow Ridge Building and Construction</span>
    </div>
    <span class="divider"></span>
    <div class="contact">
      <p class="contact__name">Your Name</p>
      <p class="contact__title">Title</p>
      <ul class="contact__list">
        <li class="contact__item">
          <svg viewBox="0 0 24 24" aria-hidden="true"><path d="M6.6 10.8a15 15 0 0 0 6.6 6.6l2.2-2.2a1 1 0 0 1 1-.25 11.4 11.4 0 0 0 3.6.57 1 1 0 0 1 1 1V20a1 1 0 0 1-1 1A17 17 0 0 1 3 4a1 1 0 0 1 1-1h3.5a1 1 0 0 1 1 1c0 1.25.2 2.45.57 3.57a1 1 0 0 1-.25 1z"/></svg>
          (123) 456-7890
        </li>
        <li class="contact__item">
          <svg viewBox="0 0 24 24" aria-hidden="true"><path d="M8 1h8a2 2 0 0 1 2 2v18a2 2 0 0 1-2 2H8a2 2 0 0 1-2-2V3a2 2 0 0 1 2-2zm0 3v14h8V4zm4 15.5a1 1 0 1 0 0 2 1 1 0 0 0 0-2z"/></svg>
          (123) 456-7890
        </li>
        <li class="contact__item">
          <svg viewBox="0 0 24 24" aria-hidden="true"><path d="M2 6a2 2 0 0 1 2-2h16a2 2 0 0 1 2 2v12a2 2 0 0 1-2 2H4a2 2 0 0 1-2-2zm2 .5V8l8 5 8-5V6.5l-8 5z"/></svg>
          yourname@harlowridge.com
        </li>
        <li class="contact__item">
          <svg viewBox="0 0 24 24" aria-hidden="true"><path d="M12 2a10 10 0 1 0 0 20 10 10 0 0 0 0-20zm6.9 6h-2.9a15 15 0 0 0-1.4-3.6A8 8 0 0 1 18.9 8zM12 4a13 13 0 0 1 1.9 4h-3.8A13 13 0 0 1 12 4zM4.3 14a8 8 0 0 1 0-4h3.4a16 16 0 0 0 0 4zm.8 2h2.9a15 15 0 0 0 1.4 3.6A8 8 0 0 1 5.1 16zM8 8H5.1a8 8 0 0 1 4.3-3.6A15 15 0 0 0 8 8zm4 12a13 13 0 0 1-1.9-4h3.8A13 13 0 0 1 12 20zm2.3-6H9.7a14 14 0 0 1 0-4h4.6a14 14 0 0 1 0 4zm.3 5.6A15 15 0 0 0 16 16h2.9a8 8 0 0 1-4.3 3.6zM16.3 14a16 16 0 0 0 0-4h3.4a8 8 0 0 1 0 4z"/></svg>
          www.harlowridge.com
        </li>
      </ul>
    </div>
    <div class="company">
      <p class="company__name">Harlow Ridge Building and Construction</p>
      <p class="company__address">00, Complex Name, Street, City 00000</p>
    </div>
  </section>

  <section class="card card--back">
    <p class="back-mark">Harlow Ridge</p>
    <p class="back-url">www.harlowridgebuilding.com</p>
  </section>
</main>
</body>
</html>
```